Front and content page design for Fitness Cookbook

I am looking for someone to Design a front cover for a Recipe book and also create an amazing layout for the book.

Its for a corporate seminar so has to be eye catching, professional and bold.

Content is complete

Target Market(s)

Industry/Entity Type

Health And Wellness

Font styles to use
Sans Serif

Requirements
Must have
• Eye catching, professional and bold.
• By Dorian as stated on the document
• Must have Tidewell Motion Logo on it.

```html
<!DOCTYPE html>
<html lang="en">
<head>
<meta charset="utf-8">
<title>Table of Contents – Fitness Cookbook</title>
<link href="https://fonts.googleapis.com/css2?family=Lato:wght@400;700;900&display=swap" rel="stylesheet">
<style>
  :root {
    --brand-blue: #1a8fd8;
    --ink: #1c2740;
    --accent-orange: #f6a21c;
    --paper: #ffffff;
  }
  html, body {
    margin: 0;
    padding: 0;
    overflow: hidden;
  }
  body {
    width: 849px;
    height: 1200px;
    background: var(--paper);
    font-family: "Lato", sans-serif;
  }
  .page {
    position: relative;
    width: 849px;
    height: 1200px;
    overflow: hidden;
    background: var(--paper);
  }
  .page-title {
    position: absolute;
    left: 46px;
    top: 22px;
    margin: 0;
    font-weight: 400;
    font-size: 66px;
    letter-spacing: -0.5px;
    color: var(--brand-blue);
  }
  .contents {
    position: absolute;
    left: 48px;
    top: 0;
    width: 740px;
  }
  .section {
    position: absolute;
    left: 0;
    width: 740px;
  }
  .section-heading {
    position: relative;
    margin: 0;
    font-weight: 400;
    font-size: 31px;
    line-height: 36px;
    color: var(--brand-blue);
    text-transform: uppercase;
    white-space: nowrap;
  }
  .section-page {
    position: absolute;
    top: 0;
  }
  .recipe-list {
    list-style: none;
    margin: 2px 0 0;
    padding: 0;
  }
  .recipe-list li {
    font-weight: 700;
    font-size: 23px;
    line-height: 36.5px;
    color: var(--ink);
  }
  .side-band {
    position: absolute;
    right: 0;
    top: 336px;
    width: 54px;
    height: 604px;
    background: var(--accent-orange);
  }
  .page-footer {
    position: absolute;
    right: 16px;
    bottom: 34px;
    display: flex;
    align-items: center;
    gap: 22px;
  }
  .brand-mark {
    display: flex;
    align-items: center;
    gap: 4px;
    font-weight: 700;
    font-size: 10px;
    color: var(--brand-blue);
  }
  .brand-mark .brand-square {
    width: 10px;
    height: 10px;
    background: var(--brand-blue);
  }
  .page-number {
    font-size: 12px;
    color: var(--ink);
  }
</style>
</head>
<body>
  <main class="page">
    <h1 class="page-title">Table of Contents</h1>

    <div class="contents">
      <section class="section" style="top:230px">
        <h2 class="section-heading">Protein and Fat Meals<span class="section-page" style="left:518px">5</span></h2>
        <ul class="recipe-list">
          <li>Homemade Beef Burger</li>
          <li>Baked Salmon and Sautéed Red Cabbage</li>
          <li>The Simple Steak</li>
          <li>Tuna Wraps</li>
        </ul>
      </section>

      <section class="section" style="top:434px">
        <h2 class="section-heading">Protein and Carbohydrate Meals<span class="section-page" style="left:668px">11</span></h2>
        <ul class="recipe-list">
          <li>Ginger and Mixed Herbs Chicken n’ Rice</li>
          <li>Fish n’ Chips</li>
          <li>Protein Porridge</li>
          <li>Post Workout Pizza</li>
        </ul>
      </section>

      <section class="section" style="top:638px">
        <h2 class="section-heading">Side Dishes<span class="section-page" style="left:470px">17</span></h2>
        <ul class="recipe-list">
          <li>Spiced Cauliflower Sauté</li>
          <li>Curried Coconut Cabbage</li>
          <li>Pan Fried Asparagus</li>
        </ul>
      </section>

      <section class="section" style="top:820px">
        <h2 class="section-heading">Healthy ‘Treats’<span class="section-page" style="left:470px">23</span></h2>
        <ul class="recipe-list">
          <li>Peanut Butter Protein Cups</li>
          <li>Chocolate Chip Cookies</li>
        </ul>
      </section>
    </div>

    <div class="side-band"></div>

    <footer class="page-footer">
      <span class="brand-mark"><span class="brand-square"></span>Tidewell Motion</span>
      <span class="page-number">3</span>
    </footer>
  </main>
</body>
</html>
```